Calm Harbor Bodywork business is seeking a Business Card Design

We are a new natural therapy business that needs a Business Card Design with an appointment card on the back.

We offer Myotherapy (muscle therapy) services and have a strong focus and commitment to helping people relieve pain and restore movement to their bodies.

I am attaching my business logo for you information.

Business card must contain my logo and have space for name, title, qualifications, phone number, email, web address

Appointment Card on the back of the card must contain space to write next appointment date, time and name of therapist and cancellation policy.

Cancellation Policy
Minimum of 24hrs notice is required prior to appointment time or full treatment fees with apply.

```html
<!DOCTYPE html>
<html lang="en">
<head>
<meta charset="utf-8">
<title>Calm Harbor Bodywork – Business &amp; Appointment Card</title>
<link rel="stylesheet" href="https://fonts.googleapis.com/css2?family=Lato:wght@400;700;900&display=swap">
<style>
  :root {
    --brand-red: #b81c33;
    --brand-brown: #4a3b34;
    --brand-green: #7dbb3c;
    --ink: #1e1e1e;
    --card: #fbfbfb;
    --stage: #2b2b2b;
  }
  * { box-sizing: border-box; margin: 0; padding: 0; }
  html, body { width: 1200px; height: 900px; overflow: hidden; }
  body {
    background: var(--stage);
    font-family: "Lato", sans-serif;
    color: var(--ink);
    position: relative;
  }
  .card {
    position: absolute;
    width: 540px;
    height: 320px;
    background: var(--card);
    box-shadow: 0 14px 30px rgba(0,0,0,.5);
    overflow: hidden;
  }
  .card--appointment { left: 50px; top: 70px; }
  .card--business { left: 610px; top: 510px; }

  /* Appointment side */
  .label {
    position: absolute;
    background: var(--brand-red);
    color: #fff;
    font-weight: 900;
    text-transform: uppercase;
    letter-spacing: .5px;
    padding: 3px 8px;
    font-size: 15px;
  }
  .label--next { left: 28px; top: 26px; font-size: 17px; }
  .label--policy { left: 28px; top: 222px; font-size: 14px; }
  .field {
    position: absolute;
    font-size: 14px;
    text-transform: uppercase;
    display: flex;
    align-items: flex-end;
    gap: 6px;
  }
  .field__line { border-bottom: 2px dotted #777; height: 12px; }
  .field--date { left: 28px; top: 72px; }
  .field--date .field__line { width: 150px; }
  .field--time { left: 262px; top: 72px; }
  .field--time .field__line { width: 200px; }
  .field--therapist { left: 28px; top: 176px; }
  .field--therapist .field__line { width: 120px; }
  .days {
    position: absolute;
    left: 28px; top: 120px;
    display: flex;
    gap: 18px;
    font-weight: 700;
    font-size: 14px;
  }
  .check { display: flex; align-items: center; gap: 5px; }
  .check__box {
    width: 18px; height: 18px;
    border: 2px solid var(--brand-red);
    border-radius: 3px;
    background: #fff;
  }
  .policy-text {
    position: absolute;
    left: 28px; top: 252px;
    width: 240px;
    font-size: 13px;
    font-weight: 700;
    line-height: 1.35;
  }

  /* Brand lockup */
  .brand { position: absolute; display: flex; align-items: center; gap: 10px; }
  .brand__mark { background: var(--brand-red); flex: none; }
  .brand__name { color: var(--brand-red); font-weight: 700; line-height: 1.05; }
  .card--appointment .brand { left: 310px; top: 212px; }
  .card--appointment .brand__mark { width: 46px; height: 46px; }
  .card--appointment .brand__name { font-size: 20px; }
  .card--business .brand { left: 26px; top: 82px; }
  .card--business .brand__mark { width: 64px; height: 64px; }
  .card--business .brand__name { font-size: 23px; }

  /* Business side */
  .tagline {
    position: absolute;
    left: 18px; top: 226px;
    width: 250px;
    text-align: center;
    color: var(--brand-red);
    font-weight: 900;
    font-size: 14px;
    line-height: 1.4;
  }
  .divider {
    position: absolute;
    left: 286px; top: 30px;
    width: 3px; height: 200px;
    background: linear-gradient(to bottom, rgba(184,28,51,0), var(--brand-red));
  }
  .person { position: absolute; left: 304px; top: 30px; }
  .person__name { color: var(--brand-red); font-weight: 900; font-size: 17px; }
  .person__title { font-weight: 700; font-size: 11px; text-transform: uppercase; }
  .contact {
    position: absolute;
    left: 304px; top: 118px;
    width: 222px;
    font-size: 12px;
  }
  .contact__address { color: var(--brand-red); font-weight: 900; font-size: 13px; line-height: 1.3; margin-bottom: 8px; }
  .contact__row { display: flex; align-items: center; gap: 7px; margin-bottom: 6px; white-space: nowrap; }
  .contact__row svg { width: 14px; height: 14px; flex: none; }
  .contact__web { color: var(--brand-red); font-weight: 900; font-size: 13px; margin-top: 6px; white-space: nowrap; }
</style>
</head>
<body>

<section class="card card--appointment" aria-label="Appointment card">
  <span class="label label--next">Next Appointment</span>
  <div class="field field--date">Date:<span class="field__line"></span></div>
  <div class="field field--time">Time:<span class="field__line"></span></div>
  <div class="days">
    <span class="check">Mon <span class="check__box"></span></span>
    <span class="check">Tue <span class="check__box"></span></span>
    <span class="check">Wed <span class="check__box"></span></span>
    <span class="check">Thu <span class="check__box"></span></span>
    <span class="check">Fri <span class="check__box"></span></span>
    <span class="check">AM <span class="check__box"></span></span>
    <span class="check">PM <span class="check__box"></span></span>
  </div>
  <div class="field field--therapist">Name of Therapist:<span class="field__line"></span></div>
  <div class="brand">
    <span class="brand__mark"></span>
    <span class="brand__name">Calm Harbor<br>Bodywork</span>
  </div>
  <span class="label label--policy">Cancellation Policy</span>
  <p class="policy-text">Minimum of 24hrs notice is required prior to appointment time or full treatment fees with apply</p>
</section>

<section class="card card--business" aria-label="Business card">
  <div class="brand">
    <span class="brand__mark"></span>
    <span class="brand__name">Calm Harbor<br>Bodywork</span>
  </div>
  <p class="tagline">Assists you to overcome<br>Acute &amp; Chronic pain &amp; injury<br>through Calm Harbor Bodywork</p>
  <span class="divider"></span>
  <div class="person">
    <p class="person__name">YOUR NAME</p>
    <p class="person__title">Designation</p>
  </div>
  <div class="contact">
    <p class="contact__address">Level 2 / 118 Juniper Lane,<br>Eastwood, VIC 3190</p>
    <p class="contact__row">
      <svg viewBox="0 0 16 16" aria-hidden="true"><path fill="#b81c33" d="M2 5c0-2 2-3 6-3s6 1 6 3v1h-3V5H5v1H2zM4 7h8l2 6H2z"/><circle cx="8" cy="10" r="1.6" fill="#fbfbfb"/></svg>
      +61 400 555 182
    </p>
    <p class="contact__row">
      <svg viewBox="0 0 16 16" aria-hidden="true"><rect x="1" y="3" width="14" height="10" fill="#b81c33"/><path d="M1 3l7 6 7-6" fill="none" stroke="#fbfbfb" stroke-width="1.3"/></svg>
      info@calmharborbodywork.com.au
    </p>
    <p class="contact__web">www.calmharborbodywork.com.au</p>
  </div>
</section>

</body>
</html>
```